Android App Design Project

Hi my name is Nadir, and I'm an android developer. I'm searching for a professional designer that can design my app.I have already launched the app and you can find it in the apptrove bazaar.

Main Requirements
- 15 sport icons
- 6 android pages
- Action bar
- Buttons and other icons

You need to do all requirements to submit a design. I need the design in both JPEG format and Photoshop PSD format. If you are interested then please download the PDF file ,it will help you a lot.
The name of the app is "MATCH VIEW Classic" you can find it in Orbix Shelf.

NOTICE: You might read that the Payment is not guaranteed if I'm not happy with the design BUT if you make a good design and you win the contest, then you become my main designer that means if I want to change or add something to the design of the app in the future I return to you "the winner" directly to make the redesign and get paid for it.

Regards.
Skype: Fadi Hamoudi "fadi48"
E-mail: fadinadir@quillpost.net

Industry/Entity Type

Tv

Requirements
Must have
• - 15 sport icons
- 6 android pages
- Action bar
- Buttons and other icons

```html
<!DOCTYPE html>
<html lang="en">
<head>
<meta charset="utf-8">
<title>MATCH VIEW Classic – Latest</title>
<link rel="stylesheet" href="https://fonts.googleapis.com/css2?family=Ubuntu+Condensed&family=Ubuntu:wght@500;700&display=swap">
<style>
  :root {
    --bar-top: #f7a35a;
    --bar-mid: #ee6f1c;
    --bar-bottom: #d9550c;
    --tab-active-top: #d8500a;
    --tab-active-bottom: #b83f05;
    --tab-edge: #9e3a06;
    --bg: #272622;
    --bg-light: #2f2e29;
    --row-line: #46443d;
    --row-shadow: #161512;
    --row-active-top: #364a5e;
    --row-active-bottom: #263646;
    --text: #ffffff;
    --thumb-frame: #1a1a17;
  }
  * { box-sizing: border-box; margin: 0; padding: 0; }
  html, body { width: 817px; height: 1200px; overflow: hidden; }
  body {
    background: radial-gradient(circle at 50% 40%, var(--bg-light), var(--bg));
    font-family: "Ubuntu Condensed", "Ubuntu", sans-serif;
    color: var(--text);
  }
  .app { position: relative; width: 817px; height: 1200px; overflow: hidden; }

  .action-bar {
    height: 102px;
    background: linear-gradient(var(--bar-top), var(--bar-mid) 50%, var(--bar-bottom));
    border-bottom: 3px solid #8a3a0a;
    position: relative;
  }
  .back-button {
    position: absolute; left: 13px; top: 22px;
    width: 77px; height: 54px;
    border-radius: 10px;
    background: linear-gradient(#fbb574, #e8671a);
    border: 2px solid #c85510;
    box-shadow: inset 0 1px 0 rgba(255,255,255,.5);
    display: flex; align-items: center; justify-content: center;
  }
  .tabs {
    position: absolute; left: 222px; top: 22px;
    width: 376px; height: 54px;
    display: flex;
    border-radius: 12px;
    border: 2px solid var(--tab-edge);
    overflow: hidden;
    box-shadow: 0 1px 0 rgba(255,255,255,.35);
  }
  .tab {
    flex: 1;
    display: flex; align-items: center; justify-content: center;
    font-family: "Ubuntu", sans-serif; font-weight: 500;
    font-size: 29px; color: var(--text);
    background: linear-gradient(#f9a865, #ea6b1c);
  }
  .tab + .tab { border-left: 2px solid var(--tab-edge); }
  .tab.is-active {
    background: linear-gradient(var(--tab-active-top), var(--tab-active-bottom));
    box-shadow: inset 0 2px 4px rgba(0,0,0,.35);
  }

  .news-list { list-style: none; }
  .news-item {
    height: 183px;
    display: flex; align-items: center;
    padding-left: 13px;
    border-top: 2px solid var(--row-line);
    border-bottom: 2px solid var(--row-shadow);
  }
  .news-item.is-selected {
    background: linear-gradient(var(--row-active-top), var(--row-active-bottom));
  }
  .news-thumb {
    flex: none;
    width: 179px; height: 166px;
    border: 2px solid var(--thumb-frame);
  }
  .thumb-green { background: linear-gradient(160deg, #2f5a22, #3f7a2c 45%, #a33a3a 80%, #d7d7d0); }
  .thumb-jersey { background: linear-gradient(150deg, #c7c7c0, #1f5a2e 40%, #2a6b38 65%, #d1a43a); }
  .thumb-red { background: linear-gradient(160deg, #3e3326, #8a2a2a 50%, #c9c4b8 80%, #2c2a24); }
  .news-text {
    margin-left: 15px; padding-right: 18px;
    font-size: 27.5px; line-height: 38px;
    letter-spacing: -0.2px;
    font-family: "Ubuntu Condensed", sans-serif;
    font-weight: 400;
    text-shadow: 0 0 0.6px #fff;
  }
</style>
</head>
<body>
<div class="app">
  <header class="action-bar">
    <div class="back-button">
      <svg width="40" height="30" viewBox="0 0 40 30" aria-label="Back">
        <path d="M2 15 L16 3 V10 H37 V20 H16 V27 Z" fill="#fff"/>
      </svg>
    </div>
    <nav class="tabs">
      <div class="tab is-active">Latest</div>
      <div class="tab">Score</div>
    </nav>
  </header>

  <ul class="news-list">
    <li class="news-item">
      <div class="news-thumb thumb-green" role="img" aria-label="Football players contesting the ball on grass"></div>
      <p class="news-text">Lorem Ipsum is simply dummy text of the printing and typesetting industry. Lorem Ipsum has been the industry's standard dummy text ever since the 1500s</p>
    </li>
    <li class="news-item is-selected">
      <div class="news-thumb thumb-jersey" role="img" aria-label="American football player in green jersey number 21"></div>
      <p class="news-text">Lorem Ipsum is simply dummy text of the printing and typesetting industry. Lorem Ipsum has been the industry's standard dummy text ever since the 1500s</p>
    </li>
    <li class="news-item">
      <div class="news-thumb thumb-red" role="img" aria-label="Football players in red and white kits in a tackle"></div>
      <p class="news-text">Lorem Ipsum is simply dummy text of the printing and typesetting industry. Lorem Ipsum has been the industry's standard dummy text ever since the 1500s</p>
    </li>
    <li class="news-item">
      <div class="news-thumb thumb-jersey" role="img" aria-label="American football player in green jersey number 21"></div>
      <p class="news-text">Lorem Ipsum is simply dummy text of the printing and typesetting industry. Lorem Ipsum has been the industry's standard dummy text ever since the 1500s</p>
    </li>
    <li class="news-item">
      <div class="news-thumb thumb-green" role="img" aria-label="Football players contesting the ball on grass"></div>
      <p class="news-text">Lorem Ipsum is simply dummy text of the printing and typesetting industry. Lorem Ipsum has been the industry's standard dummy text ever since the 1500s</p>
    </li>
    <li class="news-item">
      <div class="news-thumb thumb-red" role="img" aria-label="Football players in red and white kits in a tackle"></div>
      <p class="news-text">Lorem Ipsum is simply dummy text of the printing and typesetting industry. Lorem Ipsum has been the industry's standard dummy text ever since the 1500s</p>
    </li>
  </ul>
</div>
</body>
</html>
```